MRW (Orsolya Vendel Care) Website supporting women to live a healthy lifestyle

Hi
I'm thrilled to be working together to bring a fresh look to my website! As an Integrative Health Practitioner, my mission is to support and empower women on their journey to reclaim their health and well-being. The website should feel inviting, with a soft and nurturing energy that also radiates vibrancy and vitality.

Design & Aesthetic:

I'd love to focus on rich rose gold tones
It should feel soft and approachable yet energetic and lively.

Functional Needs:

The site will support both my coaching services
and product sales, so it’s essential to have an intuitive and user-friendly shopping experience.
I'd love some exciting interactive features that keep visitors engaged and make the journey through the site feel seamless and uplifting.

Please let me know if there’s any additional information you need from me to bring this vision to life!

Thank you for your attention to these details! Here are some ideas I like to see Layout Ideas

Hero Section: An inviting header with a subtle half-moon background for a touch of healing energy.

Navigation & Logo: Place my logo in gold on the top left and use simple navigation links with a rose gold hover effect.

Section Dividers: Use small celestial icons, like a crescent moon, as dividers to create flow and add a bit of magic.

Product & Service Section: A soft rose gold gradient background to highlight products, with circular or wave accents around images.

Footer: Deep rose gold background with a half-moon icon to end with a warm invitation to connect.

Uploading an AI-generated image (it is a bit over the top but it captures the feel I like), with a hint of spirituality and femininity, along with elements like the half moon and colors. :) I'm also uploading my logos, and I have each option available in both color schemes.

Best,
Orsolya

• Playfair Display (Headings) & Lora (Body Text)

• Cartwell

```html
<!DOCTYPE html>
<html lang="en">
<head>
<meta charset="utf-8">
<title>Orsolya Vendel Care</title>
<link href="https://fonts.googleapis.com/css2?family=Lora:wght@400;500;600;700&family=Playfair+Display:wght@700;800;900&display=swap" rel="stylesheet">
<style>
:root{
  --rose:#e2a393;
  --rose-deep:#d98f7c;
  --footer:#e9b3a4;
  --ink:#262222;
  --ink-soft:#4a3d3a;
  --white:#ffffff;
  --paper:#f8f7f7;
}
*{margin:0;padding:0;box-sizing:border-box}
html,body{width:1200px;height:3328px;overflow:hidden}
body{position:relative;font-family:'Lora',serif;color:var(--ink);background:var(--paper)}
.abs{position:absolute}
a{color:inherit;text-decoration:none}

/* hero */
.hero{left:0;top:0;width:1200px;height:743px;
  background:radial-gradient(ellipse at 66% 72%,#f1d7a8 0%,#6d8dbd 12%,#1f437e 32%,#0c2655 60%,#061636 100%)}
.header-line{left:0;top:127px;width:1200px;height:1px;background:rgba(255,255,255,.28)}
.brand{left:136px;top:24px;display:flex;align-items:center;gap:10px;color:#d9a27f;
  font-size:15px;font-weight:500;letter-spacing:.5px;text-transform:uppercase}
.brand .mark{width:60px;height:60px;border-radius:50%;border:1.5px solid #d9a27f}
.call{left:672px;top:31px;display:flex;align-items:center;gap:16px;color:var(--white);font-size:14px}
.call b{font-weight:700}
.icon-dot{width:28px;height:28px;border-radius:50%;background:var(--rose);display:flex;align-items:center;justify-content:center}
.btn{display:flex;align-items:center;justify-content:center;border-radius:30px;background:var(--rose);
  color:var(--white);font-weight:600;text-transform:uppercase;font-size:13px}
.btn-top{left:880px;top:25px;width:187px;height:38px;font-size:11.5px}
.nav{left:518px;top:88px;font-size:13px;font-weight:700;color:var(--white);text-transform:uppercase}
.nav a{position:absolute;white-space:nowrap}
.nav .active{color:var(--rose)}
.nav .active::after{content:"";position:absolute;left:8px;top:26px;width:26px;height:2px;background:var(--rose)}
.hero-title{left:136px;top:226px;font-family:'Playfair Display',serif;font-weight:800;font-size:52px;line-height:60px;color:var(--white);text-transform:uppercase}
.hero-text{left:136px;top:364px;width:340px;font-size:18.5px;line-height:25.5px;color:var(--white)}
.btn-hero{left:136px;top:470px;width:242px;height:47px}
.pager{left:1116px;top:300px;width:20px;display:flex;flex-direction:column;align-items:center;gap:8px}
.pager i{display:block;width:11px;height:11px;border-radius:50%;background:var(--white)}
.pager i.on{background:var(--rose)}

/* welcome */
.welcome-photo{left:136px;top:842px;width:440px;height:579px;border-radius:12px;
  background:linear-gradient(180deg,#c9d6e0 0%,#d9c3a8 45%,#a6825f 75%,#c9b49a 100%)}
.welcome-badge{left:512px;top:1082px;width:126px;height:126px;border-radius:50%;background:var(--paper)}
.welcome-title{left:691px;top:848px;font-weight:700;font-size:44px;line-height:51.5px;text-transform:uppercase;color:var(--ink)}
.rule{display:flex;align-items:center;gap:10px}
.rule span{display:block;width:72px;height:2px;background:var(--ink)}
.rule i{display:block;width:14px;height:14px;border-radius:50%;background:var(--rose)}
.welcome-rule{left:691px;top:1029px}
.welcome-text{left:691px;top:1068px;width:380px;font-size:16.5px;line-height:24.1px;color:var(--ink-soft)}
.btn-welcome{left:691px;top:1345px;width:177px;height:47px}

/* products */
.products{left:0;top:1460px;width:1200px;height:1123px;
  background:linear-gradient(180deg,var(--paper) 0%,#fbe9e1 22%,#f3c9ba 55%,#e7ab9a 100%)}
.divider-band{left:310px;top:1535px;width:581px;height:40px;border-radius:20px;
  background:linear-gradient(90deg,rgba(38,34,34,0),rgba(38,34,34,.18) 50%,rgba(38,34,34,0))}
.products-title{left:0;top:1688px;width:1200px;text-align:center;font-family:'Playfair Display',serif;font-weight:800;font-size:46px;color:var(--ink)}
.products-rule{left:498px;top:1772px}
.flora-left{left:0;top:2100px;width:230px;height:483px;
  background:linear-gradient(90deg,#e29a84,rgba(231,171,154,0))}
.flora-right{left:990px;top:2100px;width:210px;height:483px;
  background:linear-gradient(270deg,#e29a84,rgba(231,171,154,0))}
.card-bg{left:455px;top:2034px;width:292px;height:420px;background:var(--white);border-radius:10px}
.circle{width:278px;height:278px;border-radius:50%;border-bottom:5px solid var(--rose-deep)}
.c1{left:136px;top:1860px;background:linear-gradient(180deg,#c9ccd6 0%,#f0c890 55%,#d08f42 75%,#6a4a34 100%)}
.c2{left:462px;top:1860px;background:radial-gradient(circle at 50% 60%,#f0b8b0 0%,#e6d2c8 35%,#e9e4df 100%)}
.c3{left:788px;top:1860px;background:linear-gradient(180deg,#eac08a 0%,#f4a54c 40%,#5d5a44 70%,#3a3a2c 100%)}
.card{width:292px;text-align:center}
.card h3{font-weight:600;font-size:18.5px;line-height:27px;text-transform:uppercase;color:var(--ink-soft)}
.card p{margin:16px auto 0;width:262px;font-size:15.5px;line-height:19.7px;color:var(--ink-soft)}
.k1{left:129px;top:2176px}.k2{left:455px;top:2176px}.k3{left:781px;top:2176px}
.btn-card{top:2383px;width:152px;height:37px;background:var(--white);color:var(--ink);font-size:13px}
.btn-card.on{background:var(--rose);color:var(--white)}
.b1{left:199px}.b2{left:525px}.b3{left:851px}

/* footer */
.footer{left:0;top:2583px;width:1200px;height:745px;background:var(--footer)}
.footer-accent{left:616px;top:2617px;width:64px;height:70px;border-radius:8px;
  background:linear-gradient(110deg,#efe6df,#d9c6bb)}
.footer-brand{left:126px;top:2676px;width:235px;display:flex;flex-direction:column;align-items:center;gap:12px;
  font-size:22px;color:var(--ink);text-transform:uppercase;letter-spacing:1px;text-align:center;line-height:28px}
.footer-brand .mark{width:100px;height:100px;border-radius:50%;border:2px solid var(--ink)}
.f-head{font-weight:600;font-size:18px;text-transform:uppercase;color:var(--ink)}
.f-head::after{content:"";display:block;margin-top:12px;width:44px;height:2px;background:var(--ink)}
.h1{left:433px;top:2664px}.h2{left:728px;top:2664px}.h3{left:967px;top:2664px}
.contact-row{left:433px;display:flex;gap:20px;font-size:15.5px;line-height:22px;color:var(--ink)}
.contact-row .icon-dot{width:39px;height:39px;flex:none;background:#dc8f7b}
.r1{top:2733px}.r2{top:2818px}.r3{top:2886px}
.links{display:flex;flex-direction:column;gap:12px;font-size:14px;color:var(--ink)}
.l1{left:728px;top:2728px}.l2{left:967px;top:2728px}
.footer-line{left:136px;top:2990px;width:928px;height:1px;background:rgba(38,34,34,.2)}
.copyright{left:0;top:3040px;width:1200px;text-align:center;font-size:18px;color:var(--ink)}
.footer-scene{left:0;top:3074px;width:1200px;height:254px;
  background:linear-gradient(180deg,var(--footer) 0%,#c98d7d 40%,#8e5a4d 100%)}
</style>
</head>
<body>

<div class="abs hero" role="img" aria-label="Night sky with a glowing half moon and an open hand releasing golden sparkles"></div>
<div class="abs header-line"></div>

<div class="abs brand"><span class="mark"></span><span>Orsolya Vendel Care</span></div>
<div class="abs call">
  <span class="icon-dot"><svg width="13" height="13" viewBox="0 0 24 24"><path fill="#fff" d="M6.6 10.8a15.1 15.1 0 0 0 6.6 6.6l2.2-2.2c.3-.3.7-.4 1-.2 1.1.4 2.3.6 3.6.6.6 0 1 .4 1 1V20c0 .6-.4 1-1 1A17 17 0 0 1 3 4c0-.6.4-1 1-1h3.5c.6 0 1 .4 1 1 0 1.3.2 2.5.6 3.6.1.3 0 .7-.2 1z"/></svg></span>
  <span>CALL <b>555.0142.7788</b></span>
</div>
<a class="abs btn btn-top" href="#">Book a Consultation</a>
<nav class="abs nav">
  <a class="active" style="left:0">Home</a>
  <a style="left:85px">About Me</a>
  <a style="left:200px">Product &amp; Service</a>
  <a style="left:382px">Blog</a>
  <a style="left:464px">Contact Us</a>
</nav>

<h1 class="abs hero-title">Orsolya<br>Vendel Care</h1>
<p class="abs hero-text">Sed ut perspiciatis unde omnis iste natus error sit voluptatem accusantium doloemque laudantium, totam rem</p>
<a class="abs btn btn-hero" href="#">Book a Consultation</a>

<div class="abs pager">
  <svg width="14" height="22" viewBox="0 0 14 22"><path d="M7 21V2M1 8l6-6 6 6" stroke="#fff" stroke-width="1.6" fill="none"/></svg>
  <i class="on"></i><i></i><i></i>
  <svg width="14" height="22" viewBox="0 0 14 22"><path d="M7 1v19M1 14l6 6 6-6" stroke="#fff" stroke-width="1.6" fill="none"/></svg>
</div>

<div class="abs welcome-photo" role="img" aria-label="Smiling woman with windswept hair outdoors by the sea"></div>
<div class="abs welcome-badge"></div>
<h2 class="abs welcome-title">Welcome<br>to Orsolya<br>Vendel Care</h2>
<div class="abs rule welcome-rule"><span></span><i></i><span></span></div>
<p class="abs welcome-text">Sed ut perspiciatis unde omnis iste natus error sit voluptatem accusantium doloremque lautium, totam rem aperiam, eaque ipsa quae ab illo inventore veritatis et quasi architecto beatae vitae dicta sunt explicabo. Nemo enim ipsam voluptatem quia voluptas sit aspernatur aut odit aut fugit, sed quia consequuntur magni dolores eos qui ratione voluptatem sequi nesciunt. Neque porro quisquam est, qui dolorem ipsum quia dolor sit amet, consectetur</p>
<a class="abs btn btn-welcome" href="#">Learn More</a>

<div class="abs products"></div>
<div class="abs divider-band" role="img" aria-label="Moon phase ornament divider"></div>
<h2 class="abs products-title">Product &amp; Service</h2>
<div class="abs rule products-rule"><span></span><i></i><span></span></div>

<div class="abs flora-left" role="img" aria-label="Rose gold leaves and flowers"></div>
<div class="abs flora-right" role="img" aria-label="Rose gold leaves and blossoms"></div>

<div class="abs card-bg"></div>
<div class="abs circle c1" role="img" aria-label="Two people running on a beach at sunset"></div>
<div class="abs circle c2" role="img" aria-label="Cupped hands holding a rose quartz crystal"></div>
<div class="abs circle c3" role="img" aria-label="Woman meditating on a cliff at sunset"></div>

<div class="abs card k1"><h3>Excepteur Occaecat<br>Cupidatat Proid</h3><p>Lorem ipsum dolor sit amet, consectetur adipiscing elit, sed do eiusmod tempor incididunt ut labore et dolore magna aliqua. Ut enim ad minim veniam, quis nostrud exercitation ullamco</p></div>
<div class="abs card k2"><h3>Excepteur Occaecat<br>Cupidatat Proid</h3><p>Lorem ipsum dolor sit amet, consectetur adipiscing elit, sed do eiusmod tempor incididunt ut labore et dolore magna aliqua. Ut enim ad minim veniam, quis nostrud exercitation ullamco</p></div>
<div class="abs card k3"><h3>Excepteur Occaecat<br>Cupidatat Proid</h3><p>Lorem ipsum dolor sit amet, consectetur adipiscing elit, sed do eiusmod tempor incididunt ut labore et dolore magna aliqua. Ut enim ad minim veniam, quis nostrud exercitation ullamco</p></div>
<a class="abs btn btn-card b1" href="#">Learn More</a>
<a class="abs btn btn-card on b2" href="#">Learn More</a>
<a class="abs btn btn-card b3" href="#">Learn More</a>

<footer>
<div class="abs footer"></div>
<div class="abs footer-scene" role="img" aria-label="Woman with outstretched arms before misty mountains in rose tones"></div>
<div class="abs footer-accent" role="img" aria-label="Half moon"></div>
<div class="abs footer-brand"><span class="mark"></span><span>Orsolya Vendel<br>Care</span></div>

<h4 class="abs f-head h1">Contact Us</h4>
<h4 class="abs f-head h2">Quick Links</h4>
<h4 class="abs f-head h3">Follow Us</h4>

<div class="abs contact-row r1">
  <span class="icon-dot"><svg width="14" height="16" viewBox="0 0 24 24"><path fill="#fff" d="M12 2a7 7 0 0 0-7 7c0 5 7 13 7 13s7-8 7-13a7 7 0 0 0-7-7zm0 9.5a2.5 2.5 0 1 1 0-5 2.5 2.5 0 0 1 0 5z"/></svg></span>
  <span>Orsolya Vendel Care<br>909 Lorem ipsum dolor<br>sit amet, consectetur</span>
</div>
<div class="abs contact-row r2">
  <span class="icon-dot"><svg width="14" height="14" viewBox="0 0 24 24"><path fill="#fff" d="M6.6 10.8a15.1 15.1 0 0 0 6.6 6.6l2.2-2.2c.3-.3.7-.4 1-.2 1.1.4 2.3.6 3.6.6.6 0 1 .4 1 1V20c0 .6-.4 1-1 1A17 17 0 0 1 3 4c0-.6.4-1 1-1h3.5c.6 0 1 .4 1 1 0 1.3.2 2.5.6 3.6.1.3 0 .7-.2 1z"/></svg></span>
  <span>Call For Consultation<br><span style="font-size:18px">555.0142.7788</span></span>
</div>
<div class="abs contact-row r3">
  <span class="icon-dot"><svg width="14" height="12" viewBox="0 0 24 20"><path fill="#fff" d="M2 2h20v16H2zm2 2v1l8 5 8-5V4z"/></svg></span>
  <span>Email<br>info@orsolyavendelcare.com</span>
</div>

<div class="abs links l1"><a>Home</a><a>About me</a><a>Product &amp; Service</a><a>Blog</a><a>Contact Us</a></div>
<div class="abs links l2"><a>Kinnect</a><a>Lumigram</a><a>Pinspire</a><a>ViewStream</a><a>ProLinker</a></div>

<div class="abs footer-line"></div>
<p class="abs copyright">Copyright © 2024 Orsolya Vendel Care | All rights reserved</p>
</footer>

</body>
</html>
```